Zielgruppe
Die Velorin Akademie bietet Kurse, Seminare & Coachings im Bereich der Kommunikation / Persönlichkeitsentwicklung an.
Folgendes Angebot besteht zur Zeit:
Seminare:
- 'Erste Schritte im Dialog', eine Einführung in die Kommunikation.
- 'Heitere Töchter, ruhige Väter' zum Thema Erziehung.
- 'Reifen mit Gelassenheit', zum Thema Älter werden und den Umgang damit.
Kurse:
- 'Gewaltfreie Kommunikation', Übungsgruppe
Coaching:
- Einzelsitzungen mit Hypnose
Ps: im Anhang unter 'Angabot_Vorlage.pdf' finden Sie mehr Infos zu den einezlenen Angebote.
Aufgabenstellung
Bitte berücksichtigen Sie, dass bereits ein Logo besteht (siehe Anhang).
Vom gesamteindruck her sollte die Website aufgeräumt, übersichtlich, harmonisch, freundlich & frisch wirken.
Es wäre super, wenn die Website authentisch wirkt (und weniger '0815 Business Website').
Bitte bedenken Sie, dass die Website sich an Private richtet, die sich nach einem 'strahlenderen & unbeschwerterem Lebene sehnen'.
Wir haben bereits viele Persönlichkeiten stärken können und möchten dies auch witerhin mit viel Herzblut machen.

```html
<!DOCTYPE html>
<html lang="de">
<head>
<meta charset="utf-8">
<title>Velorin Akademie</title>
<link href="https://fonts.googleapis.com/css2?family=Raleway:ital,wght@0,400;0,500;0,600;0,700;1,400&display=swap" rel="stylesheet">
<style>
:root{
  --backdrop:#ede6df;
  --backdrop-left:#fbfaf8;
  --page:#ffffff;
  --soft:#f3efea;
  --accent:#f26d45;
  --heading:#5b4f66;
  --text:#6a6070;
  --icon:#a9774a;
  --footer:#9b8878;
  --line:#b9b0b6;
}
*{margin:0;padding:0;box-sizing:border-box}
html,body{width:1200px;height:3391px;overflow:hidden}
body{background:linear-gradient(90deg,var(--backdrop-left) 0 72px,var(--backdrop) 72px);font-family:"Raleway",sans-serif;color:var(--text);position:relative}
.page{position:absolute;left:200px;top:78px;width:901px;height:3218px;background:var(--page)}
.abs{position:absolute}
.header{left:0;top:0;width:901px;height:58px;background:linear-gradient(90deg,#efebe6,#e9e4dd)}
.brand{left:30px;top:18px;font-size:15px;font-weight:600;color:var(--heading);letter-spacing:.5px}
.nav{right:25px;top:23px;display:flex;gap:19px;font-size:9.5px;letter-spacing:.3px;color:var(--heading)}
.nav .active{color:var(--accent)}
.hero{left:0;top:58px;width:901px;height:542px;background:linear-gradient(180deg,#e7c6a2 0%,#e8a878 30%,#c98f7d 55%,#8a6f86 80%,#6d5a78 100%)}
.hero-sun{left:600px;top:230px;width:160px;height:160px;border-radius:50%;background:radial-gradient(circle,rgba(255,220,160,.9),rgba(255,170,100,0) 70%)}
.hero-title{left:0;width:901px;text-align:center;color:#fff;font-size:36px;font-weight:500;letter-spacing:5px}
.hero-sub{left:0;width:901px;text-align:center;color:#fff;font-size:18px;font-weight:500;letter-spacing:1px}
.dots{left:0;width:901px;display:flex;justify-content:center;gap:6px}
.dots span{width:8px;height:8px;border-radius:50%;border:1px solid #fff}
.dots span.on{background:#fff}
h2{font-weight:500;font-size:26px;color:var(--heading);letter-spacing:1px;text-align:center;width:901px;left:0}
.photo{background:#ccc}
.copy{font-size:10.5px;line-height:1.25;text-align:justify}
.copy p{margin-bottom:12px}
.btn{background:var(--accent);color:#fff;font-size:10.5px;font-weight:600;letter-spacing:1px;display:flex;align-items:center;justify-content:center}
.banner{left:0;top:1026px;width:901px;height:174px;background:linear-gradient(180deg,#f3e6d6,#f1d7bd 60%,#c9bcbd)}
.service{width:200px;text-align:center}
.service svg{display:block;margin:0 auto}
.service h3{font-weight:500;font-size:18px;color:var(--heading);letter-spacing:.5px;margin:14px 0 16px}
.service p{font-size:10.5px;line-height:1.25}
.offers{left:0;top:1525px;width:901px;height:1030px;background:var(--soft)}
.offer-title{font-size:12px;font-weight:700;color:var(--heading);margin-bottom:14px}
.mountain{left:0;top:2555px;width:901px;height:251px;background:linear-gradient(180deg,#d9d8db,#c6b9ad 55%,#4f4546)}
.contact-lbl{font-size:12px;letter-spacing:.5px;color:var(--heading);line-height:1.3}
.field{border:1px solid var(--line);font-size:9.5px;letter-spacing:1px;color:#9a919a;padding:8px 10px}
.footer{left:0;top:3141px;width:901px;height:77px;background:var(--footer);color:#fff;font-size:12px}
</style>
</head>
<body>
<div class="page">
  <header class="abs header">
    <div class="abs brand">Velorin Akademie</div>
    <nav class="abs nav"><span class="active">HOME</span><span>ÜBER UNS</span><span>SEMINARE</span><span>KURSE</span><span>COACHING</span><span>KONTAKT</span></nav>
  </header>

  <section class="abs hero" role="img" aria-label="Foto: Hände formen einen Rahmen um die untergehende Sonne über Bergen">
    <div class="abs hero-sun"></div>
    <div class="abs hero-title" style="top:262px">VELORIN AKADEMIE</div>
    <div class="abs hero-sub" style="top:318px">NEUE PERSPECTIVEN · NEUE HORIZONTE</div>
    <div class="abs dots" style="top:498px"><span class="on"></span><span></span><span></span></div>
  </section>

  <h2 class="abs" style="top:644px">ÜBER UNS</h2>
  <div class="abs photo" style="left:134px;top:717px;width:256px;height:223px;background:linear-gradient(135deg,#dfe3df,#c9cfc8 60%,#e9e6e2)" role="img" aria-label="Porträtfoto der Gründerin"></div>
  <div class="abs copy" style="left:435px;top:718px;width:371px">
    <p>Lorem ipsum dolor sit amet, mea cu nihil torquatos. Ad error civibus vivendum nec. Antiopam praesent sea an, id nam alii facete elaboraret.</p>
    <p>Urbanitas adolescens vituperatoribus vel in. Lorem voluptua posidonium eu sea, esse fabellas cu eam, cu vim tation nusquam. Nostrum iudicabit vix et, tota vivendo nominati has cu.</p>
    <p>Lorem ipsum dolor sit amet, mea cu nihil torquatos. Ad error civibus vivendum nec. Antiopam praesent sea an, id nam alii facete elaboraret. Urbanitas adolescens vituperatoribus vel in. Lorem voluptua posidonium eu sea, esse fabellas cu eam.</p>
  </div>
  <div class="abs btn" style="left:435px;top:910px;width:184px;height:30px">MEHR ÜBER UNS</div>

  <div class="abs banner" role="img" aria-label="Foto: Leuchtturm vor zartem Abendhimmel"></div>

  <div class="abs service" style="left:125px;top:1266px">
    <svg width="72" height="68" viewBox="0 0 72 68" fill="none" stroke="var(--icon)" stroke-width="2.5"><circle cx="36" cy="34" r="8"/><circle cx="18" cy="10" r="6"/><circle cx="54" cy="10" r="6"/><circle cx="8" cy="38" r="6"/><circle cx="64" cy="38" r="6"/><circle cx="36" cy="60" r="6"/><path d="M22 15l8 12M50 15l-8 12M14 37h14M58 37H44M36 42v12"/></svg>
    <h3>SEMINARE</h3>
    <p>Lorem ipsum dolor sit amet, mea cu nihil torquatos. Ad error civibus vivendum nec. Antiopam praesent sea an, id nam alii facete elaboraret.</p>
  </div>
  <div class="abs service" style="left:373px;top:1266px">
    <svg width="72" height="68" viewBox="0 0 72 68" fill="none" stroke="var(--icon)" stroke-width="2.5"><circle cx="36" cy="14" r="11"/><circle cx="16" cy="50" r="11"/><circle cx="56" cy="50" r="11"/><circle cx="36" cy="11" r="3"/><circle cx="16" cy="47" r="3"/><circle cx="56" cy="47" r="3"/><path d="M36 25v10l-12 8M36 35l12 8"/></svg>
    <h3>KURSE</h3>
    <p>Urbanitas adolescens vituperatoribus vel in. Lorem voluptua posidonium eu sea, esse fabellas cu eam, cu vim tation nusquam. Nostrum iudicabit vix et, tota vivendo nominati has cu.</p>
  </div>
  <div class="abs service" style="left:620px;top:1266px">
    <svg width="72" height="68" viewBox="0 0 72 68" fill="none" stroke="var(--icon)" stroke-width="2.5"><circle cx="14" cy="34" r="12"/><circle cx="58" cy="34" r="12"/><circle cx="14" cy="30" r="4"/><circle cx="58" cy="30" r="4"/><path d="M7 42c3-5 11-5 14 0M51 42c3-5 11-5 14 0M26 34h20"/></svg>
    <h3>COACHINGS</h3>
    <p>Lorem ipsum dolor sit amet, mea cu nihil torquatos. Ad civibus vivendum nec. Urbanitas adolescens vitu peratoribus vel in. Lorem voluptua posidonium eu sea, esse fabellas cu.</p>
  </div>

  <section class="abs offers">
    <h2 class="abs" style="top:52px">UNSERE AKTUELLE ANGEBOTE</h2>

    <div class="abs photo" style="left:133px;top:141px;width:257px;height:233px;background:linear-gradient(180deg,#d8d0c4,#b8ad9f 60%,#cfc6ba)" role="img" aria-label="Foto: Familie mit Kindern auf einer Brücke"></div>
    <div class="abs copy" style="left:436px;top:146px;width:372px">
      <div class="offer-title">SEMINAR: Heitere Töchter, ruhige Väter</div>
      <p><em>„Unter Erziehung versteht man die pädagogische Einflussnahme auf die Entwicklung und das Verhalten Heranwachsender“.</em> Erziehungstheorien gibt es unzählige, die das Spektrum von streng und autoritär bis hin zum Laisser-faire decken. Das selbst erlebte wird z.T. auch unreflektiert wiederholt und/oder wir verlieren uns in unzählige Ratgeber.</p>
      <p>Mithilfe der Neurowissenschaften wird uns klar, dass das oft kräftezerrende Ringen rund um die Erziehung absolut unnötig und überflüssig ist, ja sogar schädigend.</p>
    </div>
    <div class="abs btn" style="left:437px;top:332px;width:85px;height:30px">MEHR</div>

    <div class="abs photo" style="left:133px;top:432px;width:257px;height:223px;background:linear-gradient(135deg,#9a9a98,#dedcd8 45%,#6f6e6c)" role="img" aria-label="Foto: Nahaufnahme eines Uhrwerks"></div>
    <div class="abs copy" style="left:436px;top:435px;width:372px">
      <div class="offer-title">SEMINAR: Zeit und Alternativen</div>
      <p>Zeit ist ein allgegenwärtiges (und manchmal leidiges) Thema, wie z.B „keine Zeit haben“ oder „die Zeit verfliegt im Nu“. Was IST jedoch Zeit? Wie und wo nehmen wir sie wahr? Welche Auswirkungen hat das „Zeit denken“? Was wäre, wenn wir der Zeit entkommen – aussteigen – könnten? Mit welchen Folgen? Welchen Zusammenhang haben Zeit und Alter?</p>
      <p>Wir setzen uns mit unseren Vorstellungen vom Alter auseinander und stellen dem bahnbrechende Entdeckungen der Neurowissenschaften gegenüber. Aus der passiven Erwartungshaltung steigen wir in ein aktiv gewähltes altern. <em>„Älter werden ist unumgänglich. Alt werden ist optional.“</em></p>
    </div>
    <div class="abs btn" style="left:437px;top:626px;width:85px;height:30px">MEHR</div>

    <div class="abs photo" style="left:131px;top:728px;width:257px;height:223px;background:radial-gradient(circle at 55% 60%,#4e4b48,#a9a6a2 40%,#e2dfda)" role="img" aria-label="Foto: Wendeltreppe von oben"></div>
    <div class="abs copy" style="left:436px;top:731px;width:372px">
      <div class="offer-title">EINZELSITZUNGEN: Coaching mit Hypnose</div>
      <p>Einzelsitzungen...</p>
      <p>Hast du Lust, die Kraft deines Unterbewusstseins zu erfahren? Hypnose macht es erlebbar und ermöglicht, Veränderungsarbeit (wie z.B. Verhalten, Rauchen, Phobien...) erfolgreich umzusetzen</p>
    </div>
    <div class="abs btn" style="left:435px;top:922px;width:85px;height:30px">MEHR</div>
  </section>

  <div class="abs mountain" role="img" aria-label="Foto: Person sitzt auf einem Felsen über einem Tal im Gegenlicht"></div>

  <div class="abs" style="left:41px;top:2880px;width:300px;text-align:center;color:var(--heading)">
    <div style="font-size:17px;font-weight:500;letter-spacing:3px">VELORIN AKADEMIE</div>
    <div style="font-size:12.5px;font-weight:600;letter-spacing:.5px;margin-top:40px">VELORIN AKADEMIE GMBH.</div>
    <div style="font-size:13px;line-height:1.2;margin-top:16px">Lindenweg 17<br>1234 Sonnfeld</div>
    <div style="font-size:13px;line-height:1.2;margin-top:16px">TEL: 0176 987 650<br>info@velorin-akademie.ch</div>
  </div>

  <div class="abs contact-lbl" style="left:470px;top:2840px">NOCH FRAGEN, ANREGUNGEN?<br>SCHREIBEN SIE UNS!</div>
  <div class="abs field" style="left:470px;top:2880px;width:316px;height:30px">NAME</div>
  <div class="abs field" style="left:470px;top:2925px;width:316px;height:30px">E-MAIL ADRESSE</div>
  <div class="abs field" style="left:470px;top:2964px;width:316px;height:99px">NACHRICHT</div>
  <div class="abs btn" style="left:472px;top:3076px;width:163px;height:31px">SENDEN</div>

  <footer class="abs footer">
    <span class="abs" style="left:55px;top:32px">Datenschutz</span>
    <span class="abs" style="left:170px;top:32px">Impressum</span>
    <span class="abs" style="left:383px;top:32px">VELORIN AKADEMIE | 2019</span>
  </footer>
</div>
</body>
</html>
```